Vorn upkeep KT Solar Venture

Solar power system install
Services and maintenance
wiring, Rewinding and Renovation
Switch Board Upgrade
Power and lighting point
t doesn’t matter how much you spend on quality parts, your solar system will let you down if your design and installation are sub-par. Have your solar system tailored and installed by our Master Electrician and Bright Grid Guild Accredited team.

Target Market(s)

sales and installed

Industry/Entity Type

Solar install and retailer

Contact Information for Business Card

Name , Email, Phone Number ,Business address,

Font styles to use
Serif

Colors
0054AA
0677BA
7BADD7
CADEEF
E8F1F8

Requirements
Must have
• clear and bright
Nice to have
• new design
Should not have
• unclear pictures

```html
<!DOCTYPE html>
<html lang="en">
<head>
<meta charset="utf-8">
<title>Vorn upkeep – KT Solar Venture business card</title>
<link href="https://fonts.googleapis.com/css2?family=Roboto:wght@400;500;700&family=Saira+Semi+Condensed:wght@700&display=swap" rel="stylesheet">
<style>
  :root{
    --page:#2e2e2f;
    --blue-deep:#0054AA;
    --blue:#0677BA;
    --teal:#1d8fa0;
    --green:#5cb23a;
    --green-dark:#1f8a3a;
    --sun:#f3b51b;
    --band:#e9eaea;
    --card-white:#f1f1f1;
    --ink:#1c1c1c;
    --white:#ffffff;
  }
  *{margin:0;padding:0;box-sizing:border-box}
  html,body{width:1200px;height:1138px;overflow:hidden;background:var(--page)}
  body{position:relative;font-family:"Roboto",Arial,sans-serif;color:var(--ink)}
  .card{position:absolute;width:620px;height:375px;border-radius:16px;overflow:hidden}

  /* front */
  .card-front{left:274px;top:186px;
    background:linear-gradient(100deg,var(--blue) 0%,var(--teal) 45%,var(--green) 100%)}
  .front-brand{position:absolute;left:120px;top:96px;display:flex;align-items:center;gap:18px}
  .brand-dot{width:92px;height:92px;border-radius:50%;background:var(--sun)}
  .brand-name{font-family:"Saira Semi Condensed","Arial Narrow",sans-serif;font-weight:700;
    color:var(--white);font-size:42px;line-height:40px;letter-spacing:.5px;text-transform:uppercase}
  .service-band{position:absolute;left:0;top:239px;width:100%;height:73px;background:var(--band);
    display:flex;flex-direction:column;justify-content:center;align-items:center;gap:4px;
    font-size:16.5px;color:var(--ink)}
  .service-band span{padding:0 6px}
  .web-row{position:absolute;left:0;top:332px;width:100%;display:flex;justify-content:center;
    align-items:center;gap:24px;color:var(--white);font-size:15px}
  .web-row .rule{width:80px;height:2px;background:rgba(255,255,255,.7)}

  /* back */
  .card-back{left:276px;top:608px;width:618px;background:var(--card-white)}
  .back-brand{position:absolute;left:32px;top:30px;font-family:"Saira Semi Condensed","Arial Narrow",sans-serif;
    font-weight:700;font-size:30px;line-height:30px;color:var(--blue-deep);text-transform:uppercase}
  .person{position:absolute;left:32px;top:140px}
  .person-name{font-size:26px;font-weight:500;color:var(--blue-deep)}
  .person-role{font-size:16.5px;margin-top:4px}
  .address{position:absolute;left:32px;top:220px;font-size:16.5px;line-height:23px}
  .contacts{position:absolute;left:32px;top:274px;list-style:none;font-size:16.5px}
  .contacts li{display:flex;align-items:center;height:23.5px}
  .contacts svg{width:16px;height:16px;margin-right:15px;fill:var(--green-dark)}
  .back-mark{position:absolute;left:310px;top:70px;width:260px;height:260px;border-radius:50%;background:var(--sun)}
</style>
</head>
<body>
  <section class="card card-front">
    <div class="front-brand">
      <div class="brand-dot"></div>
      <div class="brand-name">Vorn upkeep<br>KT Solar Venture</div>
    </div>
    <div class="service-band">
      <div><span>Solar Power System Install</span>|<span>Wiring, Rewinding &amp; Renovation</span></div>
      <div><span>Services &amp; Maintenance</span>|<span>Switch Board Upgrade</span>|<span>Power &amp; Lighting Point</span></div>
    </div>
    <div class="web-row"><i class="rule"></i><span>www.ktsolarventure.com</span><i class="rule"></i></div>
  </section>

  <section class="card card-back">
    <div class="back-brand">Vorn upkeep<br>KT Solar Venture</div>
    <div class="person">
      <div class="person-name">Alden Reyes Marsh</div>
      <div class="person-role">Managing Director</div>
    </div>
    <div class="address">418 Harbor Lane, Millbrook,<br>Eastvale, US 204815</div>
    <ul class="contacts">
      <li><svg viewBox="0 0 16 16"><path d="M3 2h3l1.5 3.5-2 1.2a8 8 0 0 0 3.8 3.8l1.2-2L14 10v3a1 1 0 0 1-1 1A11 11 0 0 1 2 3a1 1 0 0 1 1-1z"/></svg>555-014-2290</li>
      <li><svg viewBox="0 0 16 16"><path d="M1 3h14v10H1z M2 4l6 5 6-5" fill="none" stroke="#1f8a3a" stroke-width="1.6"/></svg>alden@ktsolarventure.com</li>
      <li><svg viewBox="0 0 16 16"><circle cx="8" cy="8" r="6.5" fill="none" stroke="#1f8a3a" stroke-width="1.4"/><path d="M1.5 8h13M8 1.5c-3 3.5-3 9.5 0 13M8 1.5c3 3.5 3 9.5 0 13" fill="none" stroke="#1f8a3a" stroke-width="1.2"/></svg>www.ktsolarventure.com</li>
    </ul>
    <div class="back-mark"></div>
  </section>
</body>
</html>
```